Website design for lighting products company

We want a design for our website. The website is for a company that sells lighting products. The structure is similar to the below website. We really like their design as well: www.palvenorlighting.com

Industry/Entity Type

Lighting

Number of Pages Required

5+ page

Colors

Designer to choose colors to be used in the design.

Requirements
Must have
• Simple design

```html
<!DOCTYPE html>
<html lang="en">
<head>
<meta charset="utf-8">
<title>Orva Lighting</title>
<link href="https://fonts.googleapis.com/css2?family=Montserrat:wght@400;500;600;700;800&family=Lato:wght@400;700&display=swap" rel="stylesheet">
<style>
:root{
  --coral:#c9654f;
  --navy:#2a3a5a;
  --ink:#111;
  --text:#555;
  --blush:#fcf4f2;
  --footer:#1d1d1d;
  --white:#fff;
}
*{margin:0;padding:0;box-sizing:border-box}
html,body{width:1200px;height:3479px;overflow:hidden;background:var(--white)}
body{position:relative;font-family:"Montserrat",sans-serif;color:var(--ink)}
.abs{position:absolute}
.header{left:0;top:0;width:1200px;height:105px;background:var(--white)}
.logo{left:112px;top:26px;font-size:38px;font-weight:600;color:var(--coral);letter-spacing:.5px}
.nav a{position:absolute;top:70px;font-size:15px;font-weight:500;color:var(--ink);text-decoration:none}
.nav a.active{color:var(--coral);text-decoration:underline}
.shop{left:896px;top:14px;width:189px;height:40px;border-radius:20px;background:var(--coral);color:var(--white);font-size:17px;font-weight:600;display:flex;align-items:center;justify-content:center;gap:8px}
.hero{left:0;top:105px;width:1200px;height:631px;background:radial-gradient(circle at 70% 40%,#a07a5a 0%,#5d5a60 45%,#3a4458 100%)}
.hero-title{left:115px;top:322px;font-size:62px;font-weight:800;color:var(--white)}
.hero-text{left:112px;top:414px;width:530px;font-size:16.5px;line-height:26px;color:var(--white)}
.btn{display:block;width:216px;height:44px}
.btn span{position:absolute;left:50px;top:11px;font-size:17px;font-weight:500;color:var(--white)}
.h2{font-size:42px;font-weight:800;color:var(--ink)}
.para{font-size:16.5px;line-height:26px;color:var(--text)}
.frame{left:119px;top:1378px;width:321px;height:325px}
.caption{left:119px;top:1736px;width:325px;text-align:center;font-size:16px;font-weight:600;color:#444}
.tile{position:absolute}
.lc-title{left:318px;top:2434px;width:364px;text-align:center;font-size:28px;font-weight:800;line-height:36px;color:var(--white)}
.lc-sub{left:318px;top:2513px;width:364px;text-align:center;font-size:14px;color:var(--white)}
.lc-btn{left:372px;top:2554px;width:256px;height:40px;border:1.5px solid var(--white);border-radius:20px;color:var(--white);font-size:16px;font-weight:500;display:flex;align-items:center;justify-content:center}
.input{left:108px;top:2990px;width:500px;height:51px;background:linear-gradient(90deg,#dcdcdc 70%,rgba(220,220,220,0));font-size:15px;font-weight:700;color:#555;padding:17px 0 0 23px}
.footer{left:0;top:3189px;width:1200px;height:290px;background:var(--footer);color:var(--white);font-family:"Lato",sans-serif}
.footer h3{position:absolute;font-family:"Montserrat",sans-serif;font-size:16px;font-weight:700;color:#eee}
.footer a,.footer p{position:absolute;font-size:14px;color:#ddd;text-decoration:none}
.footer .dot{position:absolute;width:16px;height:16px;border-radius:50%;background:#fff}
</style>
</head>
<body>

<header class="abs header">
  <div class="abs logo">ORVA LIGHTING</div>
  <nav class="nav">
    <a class="active" style="left:558px">HOME</a>
    <a style="left:658px">ABOUT US</a>
    <a style="left:790px">SERVICES</a>
    <a style="left:919px">BLOG</a>
    <a style="left:1013px">CONTACT</a>
  </nav>
  <div class="abs shop">
    <svg width="18" height="16" viewBox="0 0 18 16"><path d="M0 1h3l2 9h10l2-7H5" fill="none" stroke="#fff" stroke-width="2"/><circle cx="7" cy="14" r="1.6" fill="#fff"/><circle cx="14" cy="14" r="1.6" fill="#fff"/></svg>
    SHOP NOW
  </div>
</header>

<section class="abs hero" role="img" aria-label="Photo of hanging filament bulbs among dried flowers"></section>
<svg class="abs" style="left:0;top:105px" width="1200" height="631">
  <path d="M70 390 58 401 70 412" stroke="#fff" stroke-width="3" fill="none"/>
  <path d="M1109 390 1121 401 1109 412" stroke="#fff" stroke-width="3" fill="none"/>
</svg>
<h1 class="abs hero-title">ORVA LIGHTING</h1>
<p class="abs hero-text">Lorem ipsum dolor sit amet, consectetur adipiscing elit, sed do eiusmod tempor incididunt ut labore et dolore magna aliqua.</p>
<div class="abs btn" style="left:112px;top:511px">
  <svg width="216" height="44"><polygon points="14,0 180,0 166,44 0,44" fill="var(--navy)"/><polygon points="186,0 214,0 200,44 172,44" fill="var(--coral)"/></svg>
  <span>READ MORE</span>
</div>
<svg class="abs" style="left:0;top:736px" width="1200" height="44"><polygon points="0,0 1000,0 0,42" fill="var(--coral)"/></svg>

<h2 class="abs h2" style="left:112px;top:902px">ABOUT US</h2>
<p class="abs para" style="left:112px;top:984px;width:476px">Lorem ipsum dolor sit amet, consectetur adipiscing elit, sed do eiusmod tempor incididunt ut labore et dolore magna aliqua. Quis ipsum suspendisse ultrices gravida. Risus commodo viverra maecenas accumsan lacus vel facilisis. Lorem ipsum dolor sit amet, consectetur adipiscing elit, sed do eiusmod tempor incididunt ut labore et dolore magna aliqua.</p>
<div class="abs btn" style="left:112px;top:1190px">
  <svg width="216" height="44"><polygon points="14,0 180,0 166,44 0,44" fill="var(--navy)"/><polygon points="186,0 214,0 200,44 172,44" fill="var(--coral)"/></svg>
  <span>READ MORE</span>
</div>
<div class="abs" style="left:804px;top:896px;width:284px;height:304px;background:var(--navy)"></div>
<div class="abs" style="left:663px;top:927px;width:388px;height:243px;background:linear-gradient(90deg,#2a2520,#b89a6a 45%,#3a3028 70%,#d8b878 90%,#2a2520)" role="img" aria-label="Photo of wall lights casting beams on a textured wall"></div>

<svg class="abs" style="left:0;top:1295px" width="1200" height="520"><path d="M0 117 1170 4 Q1198 2 1198 30 L1200 460 16 516 Q8 516 6 500 Z" fill="var(--blush)"/></svg>
<svg class="abs frame" width="321" height="325">
  <path d="M95 1H1v323h95M226 1h94v323h-94" fill="none" stroke="var(--coral)" stroke-width="2"/>
</svg>
<div class="abs" style="left:168px;top:1425px;width:226px;height:226px;border-radius:50%;background:radial-gradient(circle at 40% 30%,#e0306a,#a0105a 50%,#40104a)" role="img" aria-label="Photo of red emergency lights"></div>
<svg class="abs" style="left:64px;top:1517px" width="430" height="42">
  <circle cx="20" cy="21" r="20" fill="var(--coral)"/><path d="M24 13 16 21 24 29" stroke="#fff" stroke-width="3.5" fill="none"/>
  <circle cx="406" cy="21" r="20" fill="var(--coral)"/><path d="M402 13 410 21 402 29" stroke="#fff" stroke-width="3.5" fill="none"/>
</svg>
<div class="abs caption">EMERGENCY LIGHTS</div>
<h2 class="abs h2" style="left:597px;top:1400px">SERVICES</h2>
<p class="abs para" style="left:598px;top:1481px;width:488px;text-align:justify">Lorem ipsum dolor sit amet, consectetur adipiscing elit, sed do eiusmod tempor incididunt ut labore et dolore magna aliqua. Quis ipsum suspendisse ultrices gravida. Risus commodo viverra Lorem ipsum dolor sit amet, consectetur adipiscing elit, sed do eiusmod tempor incididunt ut labore et dolore magna aliqua. Quis ipsum suspendisse ultrices gravida.</p>
<div class="abs btn" style="left:592px;top:1680px">
  <svg width="216" height="44"><polygon points="14,0 180,0 166,44 0,44" fill="var(--navy)"/><polygon points="186,0 214,0 200,44 172,44" fill="var(--coral)"/></svg>
  <span>READ MORE</span>
</div>

<h2 class="abs h2" style="left:0;top:1848px;width:1200px;text-align:center">OUR PROJECTS</h2>
<div class="tile" style="left:0;top:1962px;width:505px;height:331px;background:linear-gradient(135deg,#c02030,#5a2030 50%,#8090a0)" role="img" aria-label="Photo of wet street reflecting red light"></div>
<div class="tile" style="left:522px;top:1962px;width:268px;height:331px;background:linear-gradient(160deg,#4a4030,#8a8068 50%,#a8a090)" role="img" aria-label="Photo of lit stone steps"></div>
<div class="tile" style="left:807px;top:1962px;width:393px;height:331px;background:radial-gradient(circle at 55% 40%,#b89a70,#2a3020 60%,#1a1a18)" role="img" aria-label="Photo of an outdoor pergola with string lights over a table"></div>
<div class="tile" style="left:0;top:2312px;width:301px;height:413px;background:radial-gradient(circle at 60% 25%,#ffd080,#8a3010 35%,#2a1008 75%)" role="img" aria-label="Photo of a park lamp at night"></div>
<div class="tile" style="left:318px;top:2312px;width:364px;height:413px;background:linear-gradient(160deg,#d88080,#c86060 50%,#b85858)" role="img" aria-label="Photo of hands holding a lighting control tablet"></div>
<div class="abs lc-title">LIGHTING<br>CONTROLS</div>
<div class="abs lc-sub">starting since 1998</div>
<div class="abs lc-btn">POST A PROECT LIKE THIS</div>
<div class="tile" style="left:700px;top:2312px;width:500px;height:413px;background:radial-gradient(circle at 50% 45%,#f0a020,#a04010 35%,#1a0a05 75%)" role="img" aria-label="Photo of glowing hanging filament bulbs"></div>

<div class="abs" style="left:0;top:2743px;width:1200px;height:446px;background:linear-gradient(90deg,#fff 45%,#c0d8a0 62%,#4a7a2a 80%,#2a4a18)" role="img" aria-label="Photo of a garden lamp among green foliage"></div>
<h2 class="abs h2" style="left:108px;top:2814px">NEWS LETTER</h2>
<p class="abs para" style="left:112px;top:2889px;width:460px">Lorem ipsum dolor sit amet, consectetur adipiscing elit, sed do eiusmod tempor incididunt ut labore et dolore magna aliqua. Quis ipsum suspendisse .</p>
<div class="abs input">Enter Your MAIL ID</div>
<svg class="abs" style="left:571px;top:2996px" width="40" height="40"><circle cx="20" cy="20" r="19" fill="var(--coral)"/><path d="M16 12 24 20 16 28" stroke="#fff" stroke-width="3.5" fill="none"/></svg>

<footer class="abs footer">
  <h3 style="left:115px;top:58px;font-size:21px;font-weight:500">ABOUT US</h3>
  <p style="left:115px;top:102px;width:360px;font-size:12.5px;line-height:20px">Lorem ipsum dolor sit amet, consectetur adipiscing elit, sed do eiusmod tempor incididunt ut labore et dolore magna aliqua. Quis ipsum suspendisse ultrices gravida. Risus commodo viverra maecenas accumsan lacus vel facilisis.</p>
  <h3 style="left:542px;top:52px">COMPANY</h3>
  <a style="left:542px;top:93px">Home</a>
  <a style="left:542px;top:117px">About us</a>
  <a style="left:542px;top:144px">Services</a>
  <h3 style="left:695px;top:52px">RESOURCES</h3>
  <a style="left:695px;top:93px">Why us</a>
  <a style="left:695px;top:117px">Support</a>
  <a style="left:695px;top:146px">Terms and Conditions</a>
  <a style="left:695px;top:173px">Privacy</a>
  <a style="left:695px;top:201px">Contact us</a>
  <h3 style="left:884px;top:52px">GET IN TOUCH</h3>
  <span class="dot" style="left:895px;top:70px"></span><a style="left:923px;top:69px">Microblog</a>
  <span class="dot" style="left:895px;top:102px"></span><a style="left:923px;top:101px">Social Feed</a>
  <span class="dot" style="left:895px;top:132px"></span><a style="left:923px;top:131px">Pro Network</a>
  <span class="dot" style="left:895px;top:163px"></span><a style="left:923px;top:162px">Photo Stream</a>
  <p style="left:0;top:256px;width:1200px;text-align:center;font-size:15px">Copyright @ 2019 All right reserved</p>
</footer>

</body>
</html>
```